Website for Apartment Rental in Prague

I would like to create designs of my website focused on luxury apartment rentals in Prague, Czech Republic. I created initial mock-ups, They are all attached. I need to design homepage and subpage. The mock-ups were created by combining elements from different websites that I liked but I need you to create a design that is unique and original. The attached files a only a guidance for the structure of the website but not for the design. Try to be creative.

Apartment

```html
<!DOCTYPE html>
<html lang="en">
<head>
<meta charset="utf-8">
<title>Vltava Suites – Luxury Apartment Rentals in Prague</title>
<link rel="stylesheet" href="https://fonts.googleapis.com/css2?family=Libre+Baskerville:wght@700&family=Questrial&family=Open+Sans:wght@400;600;700&display=swap">
<style>
:root{
  --gold:#b49b5c;
  --gold-soft:#c2ab70;
  --gold-dark:#8e7840;
  --ink:#111111;
  --ink-soft:#1c1c1c;
  --text:#333333;
  --muted:#666666;
  --white:#ffffff;
  --paper:#ffffff;
}
*{box-sizing:border-box;margin:0;padding:0}
html,body{width:1200px;height:4412px;overflow:hidden;background:var(--paper)}
body{font-family:"Open Sans",Arial,sans-serif;color:var(--text);position:relative}
.section{position:absolute;left:0;width:1200px}
.display{font-family:"Questrial",Arial,sans-serif;font-weight:400;letter-spacing:1px}

/* header + hero */
.hero{top:0;height:676px;background:linear-gradient(180deg,#7d9bc0 0%,#a9bfd6 30%,#8b8f86 62%,#5b5246 100%)}
.site-header{position:absolute;top:0;left:0;width:1200px;height:103px;background:rgba(255,255,255,.55);display:flex;align-items:center;padding:0 76px}
.brand{font-family:"Questrial",Arial,sans-serif;font-size:26px;color:var(--ink);letter-spacing:3px}
.nav{margin-left:auto;display:flex;gap:22px;align-items:center;font-size:14px;color:var(--ink);text-transform:uppercase}
.nav svg{width:18px;height:18px}
.hero-copy{position:absolute;top:262px;width:100%;text-align:center;color:var(--white)}
.hero-title{font-family:"Libre Baskerville",Georgia,serif;font-size:46px;color:var(--ink)}
.hero-rule{width:600px;height:2px;background:var(--ink);margin:18px auto}
.hero-sub{font-family:"Libre Baskerville",Georgia,serif;font-size:26px;color:var(--ink)}

/* booking */
.booking{top:676px;height:221px;background:var(--gold);display:flex}
.booking-badge{width:426px;background:var(--ink);padding:74px 0 0 78px}
.booking-badge h2{font-size:40px;color:var(--gold);font-weight:700}
.booking-badge p{color:var(--white);font-size:17px;margin-top:6px}
.booking-form{padding:28px 0 0 30px;color:var(--white);font-size:15px}
.field-row{display:flex;gap:14px;align-items:flex-end}
.field label{display:block;margin-bottom:6px}
.input{height:46px;background:var(--white);color:var(--text);font-size:14px;display:flex;align-items:center;padding:0 12px;justify-content:space-between}
.btn-dark{background:var(--ink);color:var(--white);font-size:15px;font-weight:700;display:inline-flex;align-items:center;justify-content:center;text-transform:uppercase}

/* vision */
.vision{top:897px;height:388px;text-align:center}
.vision h2{font-size:46px;color:var(--gold);margin-top:48px;font-weight:700}
.vision h3{font-size:20px;letter-spacing:1px;font-weight:700;color:var(--ink);margin-top:6px}
.vision p{font-size:14px;line-height:26px;color:var(--muted);margin-top:22px}
.vision .btn-dark{width:282px;height:54px;margin-top:26px;border-radius:6px;font-weight:400;font-size:20px}

/* why */
.why{top:1285px;height:973px;background:var(--ink)}
.why h2{position:absolute;left:78px;top:44px;font-size:40px;color:var(--gold);font-weight:700}
.why-side{position:absolute;left:700px;top:90px;width:500px;height:883px;background:var(--gold)}
.listing{position:absolute;left:0;width:1200px;height:200px}
.listing-copy{position:absolute;left:78px;width:290px;color:var(--white)}
.listing-copy h4{font-size:18px;font-weight:400;line-height:28px}
.listing-copy p{font-size:13px;line-height:20px;color:#bbb;margin-top:16px}
.listing-photo{position:absolute;left:397px;top:0;width:276px;height:190px}
.listing-info{position:absolute;left:720px;color:var(--ink)}
.price{font-size:22px;font-weight:700;color:var(--white)}
.spec{display:flex;align-items:center;gap:16px;font-size:13px;color:var(--ink);margin-top:12px}
.spec svg{width:26px;height:26px}
.actions{display:flex;gap:14px;margin-top:22px}
.btn-outline{width:158px;height:40px;border:1.5px solid var(--ink);color:var(--ink);display:flex;align-items:center;justify-content:center;font-size:14px;text-transform:uppercase}
.actions .btn-dark{width:158px;height:40px;font-weight:400;font-size:14px}
.more-rent{position:absolute;left:808px;top:878px;width:282px;height:54px;border:2px solid rgba(255,255,255,.75);color:var(--white);font-size:20px;display:flex;align-items:center;justify-content:center;text-transform:uppercase}

/* need to know */
.know{top:2258px;height:412px;text-align:center}
.know h2{font-size:40px;color:var(--gold);margin-top:54px;font-weight:700}
.know-grid{display:flex;justify-content:center;gap:70px;margin-top:44px}
.know-item{width:270px}
.know-item svg{width:110px;height:110px}
.know-item h4{font-size:20px;color:var(--ink);margin-top:18px;font-weight:600}
.know-item p{font-size:13px;line-height:20px;color:var(--muted);margin-top:8px}

/* interiors */
.interiors{top:2670px;height:417px;background:linear-gradient(180deg,#c8b27a 0%,#b49b5c 55%,#9e8650 100%);text-align:center;color:var(--ink)}
.lamp{width:104px;height:104px;margin:46px auto 0;border-radius:50%;background:var(--white);display:flex;align-items:center;justify-content:center}
.interiors p{font-size:14px;line-height:26px;width:980px;margin:28px auto 0}
.interiors h4{font-size:20px;font-weight:700;margin-top:18px}
.interiors .by{font-size:15px;margin-top:4px}

/* gallery */
.gallery{top:3087px;height:809px;text-align:center}
.gallery h2{font-size:40px;color:var(--gold);margin-top:54px;font-weight:700}
.gallery .intro{font-size:15px;line-height:26px;color:var(--text);width:820px;margin:18px auto 0}
.gallery-grid{position:absolute;left:80px;top:200px;width:1040px;display:grid;grid-template-columns:repeat(3,1fr);gap:24px 24px}
.tile{height:230px}
.tile-feature{background:var(--gold);border:14px solid var(--gold);outline:1.5px solid rgba(255,255,255,.8);outline-offset:-10px;color:var(--white);display:flex;flex-direction:column;align-items:center;justify-content:center}
.tile-feature h5{font-size:19px;font-weight:700}
.tile-feature span{margin-top:16px;width:156px;height:40px;border:1.5px solid var(--white);display:flex;align-items:center;justify-content:center;font-size:14px}
.gallery .btn-dark{position:absolute;left:504px;top:697px;width:192px;height:52px;border-radius:6px;font-weight:400;font-size:20px}

/* cta */
.cta{top:3896px;height:138px;background:var(--gold);display:flex;align-items:center;justify-content:center;gap:40px}
.cta h3{font-size:38px;color:var(--white);font-weight:400}
.cta .btn-dark{width:190px;height:54px;font-weight:400;font-size:20px}

/* footer */
.footer{top:4034px;height:378px;background:var(--ink);color:#ddd;font-size:13px}
.col{position:absolute;top:40px}
.col h6{font-size:15px;color:var(--gold);font-weight:700;text-transform:uppercase;margin-bottom:18px}
.sitemap li{list-style:none;line-height:25px}
.sitemap li::before{content:"";display:inline-block;width:6px;height:6px;border-radius:50%;background:#ddd;margin-right:12px;vertical-align:middle}
.contact-line{display:flex;gap:14px;margin-bottom:22px;line-height:20px}
.contact-line svg{width:22px;height:22px;flex:none}
.contact-line .gold{color:var(--gold)}
.socials{display:flex;gap:10px}
.socials span{width:40px;height:40px;border-radius:50%;background:var(--gold);display:block}
.news p{line-height:21px;width:236px}
.news .input{width:236px;height:38px;margin-top:12px;font-size:12px}
.subscribe{margin-top:20px;width:190px;height:46px;border:1.5px solid var(--white);border-radius:6px;display:flex;align-items:center;justify-content:center;color:var(--white);font-size:16px;text-transform:uppercase}
.footer-brand{font-family:"Questrial",Arial,sans-serif;font-size:30px;color:var(--gold);letter-spacing:3px;line-height:40px}
.footer-brand + p{margin-top:18px;line-height:22px}
</style>
</head>
<body>

<section class="section hero" role="img" aria-label="Photo of a bright apartment terrace with lounge furniture overlooking the Prague city skyline">
  <header class="site-header">
    <div class="brand">VLTAVA SUITES</div>
    <nav class="nav">
      <svg viewBox="0 0 20 20"><path d="M2 10 10 3l8 7h-3v7h-4v-5H9v5H5v-7z" fill="#b49b5c"/></svg>
      <span>Apartments</span><span>Location</span><span>Services</span><span>Gallery</span><span>News</span><span>Exclusive Offers &amp; Tours</span><span>For Families</span><span>Contact Us</span>
    </nav>
  </header>
  <div class="hero-copy">
    <h1 class="hero-title">Luxury Apartment Rentals In Prague</h1>
    <div class="hero-rule"></div>
    <p class="hero-sub">Price From 150usd Per Night, Including Tax</p>
  </div>
</section>

<section class="section booking">
  <div class="booking-badge display">
    <h2>OFFICIAL SITE</h2>
    <p>Best Price Guaranteed</p>
  </div>
  <div class="booking-form">
    <div class="field-row">
      <div class="field"><label>Check in date :</label><div class="input" style="width:166px">11 / 17 / 2017</div></div>
      <div class="field"><label>Check out date :</label><div class="input" style="width:166px">11 / 18 / 2017</div></div>
      <div class="field"><label>Adults :</label><div class="input" style="width:100px">2 <span>▾</span></div></div>
      <div class="field"><label>Children :</label><div class="input" style="width:100px">0 <span>▾</span></div></div>
      <div class="field"><label>Infants :</label><div class="input" style="width:100px">0 <span>▾</span></div></div>
    </div>
    <div class="field-row" style="margin-top:10px">
      <div class="field"><label>Promotional code</label><div class="input" style="width:210px"></div></div>
      <div class="btn-dark" style="width:184px;height:46px">Check Availibility</div>
      <span style="font-size:20px;padding-bottom:10px">or</span>
      <div class="input" style="width:214px">Select rental Unit <span>▾</span></div>
    </div>
  </div>
</section>

<section class="section vision">
  <h2 class="display">A DIFFERENT VISION OF</h2>
  <h3>TRAVELLING</h3>
  <p>Something spectacular has arrived in the heart of Europe.<br>
  Steps From Old Town, this rental experience is curated with world class amenities , exemplary style and a level of convenience<br>
  You have to experience to believe. Experience the different vision of luxury in center of Prague.</p>
  <div class="btn-dark">More About Prague</div>
</section>

<section class="section why">
  <h2 class="display">WHY PRAGUE APARTMENTS</h2>
  <div class="why-side"></div>

  <div class="listing" style="top:130px">
    <div class="listing-copy"><h4>BRAND NEW Luxury Living<br>Stunning Contemporary Design</h4><p>The 22nd floor is dedicated to color...</p></div>
    <div class="listing-photo" role="img" aria-label="Photo of a white open-plan living and dining room" style="background:linear-gradient(135deg,#e8e4dc,#b9b1a2)"></div>
    <div class="listing-info"><div class="price">$150 USD</div>
      <div class="spec"><svg viewBox="0 0 24 24"><path d="M3 20V6M21 20v-6H3M3 14V10h8v4M11 12h10" stroke="#111" stroke-width="2" fill="none"/></svg>1 Bedroom</div>
      <div class="spec"><svg viewBox="0 0 24 24"><circle cx="12" cy="7" r="5" fill="#111"/><path d="M3 23a9 8 0 0 1 18 0z" fill="#111"/></svg>max 4 people</div>
      <div class="actions"><div class="btn-outline">Detail</div><div class="btn-dark">Book Now</div></div></div>
  </div>

  <div class="listing" style="top:372px">
    <div class="listing-copy"><h4>BRAND NEW Luxury Living<br>Apartment in the center of Prague.</h4><p>Recognized with Voyage Digest 2017 Readers' Choice Award #1 Hotel in The World...</p></div>
    <div class="listing-photo" role="img" aria-label="Photo of a living room with panoramic city windows" style="background:linear-gradient(135deg,#c8d3dd,#7f8d9a)"></div>
    <div class="listing-info"><div class="price">$150 USD</div>
      <div class="spec"><svg viewBox="0 0 24 24"><path d="M3 20V6M21 20v-6H3M3 14V10h8v4M11 12h10" stroke="#111" stroke-width="2" fill="none"/></svg>1 Bedroom</div>
      <div class="spec"><svg viewBox="0 0 24 24"><circle cx="12" cy="7" r="5" fill="#111"/><path d="M3 23a9 8 0 0 1 18 0z" fill="#111"/></svg>max 4 people</div>
      <div class="actions"><div class="btn-outline">Detail</div><div class="btn-dark">Book Now</div></div></div>
  </div>

  <div class="listing" style="top:614px">
    <div class="listing-copy"><h4>Expedition Prague! Top Location<br>Brand New Apartment...</h4><p>For your Management committee, showroom session, Incentive trip, Product Launch privatization...</p></div>
    <div class="listing-photo" role="img" aria-label="Photo of a monochrome modern lounge interior" style="background:linear-gradient(135deg,#d9d9d9,#555)"></div>
    <div class="listing-info"><div class="price">$150 USD</div>
      <div class="spec"><svg viewBox="0 0 24 24"><path d="M3 20V6M21 20v-6H3M3 14V10h8v4M11 12h10" stroke="#111" stroke-width="2" fill="none"/></svg>1 Bedroom</div>
      <div class="spec"><svg viewBox="0 0 24 24"><circle cx="12" cy="7" r="5" fill="#111"/><path d="M3 23a9 8 0 0 1 18 0z" fill="#111"/></svg>max 4 people</div>
      <div class="actions"><div class="btn-outline">Detail</div><div class="btn-dark">Book Now</div></div></div>
  </div>

  <div class="more-rent">View Mor For Rent</div>
</section>

<section class="section know">
  <h2 class="display">NEED TO KNOW</h2>
  <div class="know-grid">
    <div class="know-item">
      <svg viewBox="0 0 110 110" fill="none" stroke="#b49b5c" stroke-width="4"><rect x="22" y="22" width="40" height="80"/><rect x="62" y="44" width="26" height="58"/><path d="M32 34h6M46 34h6M32 50h6M46 50h6M32 66h6M46 66h6M32 82h6M46 82h6M70 58h10M70 74h10"/></svg>
      <h4>APARTMENT</h4><p>Also available to rent all the apartments together for companies or larger group.</p>
    </div>
    <div class="know-item">
      <svg viewBox="0 0 110 110" fill="none" stroke="#b49b5c" stroke-width="4"><path d="M42 14l3 6 6 1-4 4 1 6-6-3-6 3 1-6-4-4 6-1zM62 10l3 6 6 1-4 4 1 6-6-3-6 3 1-6-4-4 6-1z" stroke-width="2.5"/><rect x="22" y="36" width="52" height="64"/><path d="M32 52h8M46 52h18M32 68h8M46 68h18M32 84h8"/><circle cx="78" cy="80" r="16"/><path d="M78 72v8h6"/></svg>
      <h4>CHECK - OUT</h4><p>12 noon, earlies check- in, 3pm - both are flexible,<br>by arrangement.</p>
    </div>
    <div class="know-item">
      <svg viewBox="0 0 110 110" fill="none" stroke="#b49b5c" stroke-width="4"><circle cx="55" cy="26" r="12"/><path d="M35 62a20 18 0 0 1 40 0z"/><path d="M30 74l4 8 8 1-6 6 2 8-8-4-8 4 2-8-6-6 8-1zM55 74l4 8 8 1-6 6 2 8-8-4-8 4 2-8-6-6 8-1zM80 74l4 8 8 1-6 6 2 8-8-4-8 4 2-8-6-6 8-1z" stroke-width="3"/></svg>
      <h4>RATES</h4><p>price from 150usd per night,<br>including tax.</p>
    </div>
  </div>
</section>

<section class="section interiors" role="img" aria-label="Gold-toned photo of a city skyline at dusk behind the interiors statement">
  <div class="lamp"><svg viewBox="0 0 60 60" width="60" height="60" fill="none" stroke="#b49b5c" stroke-width="3"><path d="M20 8h20l6 24H14z"/><path d="M30 32v20M20 52h20"/></svg></div>
  <p>Maison Lumen apartments offers short term and as well as long term options in our studio apartments and our one bedroom apartment homes. Our Luxurious apartments and high Quality customer services have allowed us to dominate the prague apartment market with a proven track record. Our years of experience and knowledge have made us a premier apartment rental company as we continue to stress the importance of services individuals and corporation who are seeking the finest accommodations.</p>
  <h4>Interiors Designed</h4>
  <div class="by">by Maison Lumen</div>
</section>

<section class="section gallery">
  <h2 class="display">GALLERY</h2>
  <p class="intro">Lorem Ipsum is simply dummy text of the printing and typesetting industry. Lorem Ipsum has been the industry's standard dummy text ever since the when an unknown printer took.</p>
  <div class="gallery-grid">
    <div class="tile" role="img" aria-label="Photo of a grey living room with sofas" style="background:linear-gradient(135deg,#cfcac2,#6e675e)"></div>
    <div class="tile tile-feature"><h5>LOREM IPSUM TEXT</h5><span>DETAIL</span></div>
    <div class="tile" role="img" aria-label="Photo of a warm-lit lounge with wooden floor" style="background:linear-gradient(135deg,#e9dcc6,#a98a62)"></div>
    <div class="tile" role="img" aria-label="Photo of a villa terrace with pool by the sea" style="background:linear-gradient(180deg,#6fa0c9,#d9c8ad)"></div>
    <div class="tile" role="img" aria-label="Photo of a games room with pool table" style="background:linear-gradient(135deg,#b8a48a,#5a4634)"></div>
    <div class="tile" role="img" aria-label="Photo of a balcony with sea and city view" style="background:linear-gradient(180deg,#7fa9cf,#a8a29a)"></div>
  </div>
  <div class="btn-dark">View More</div>
</section>

<section class="section cta">
  <h3 class="display">Official Site Best Price Guaranteed</h3>
  <div class="btn-dark">Book Now</div>
</section>

<footer class="section footer">
  <div class="col" style="left:80px">
    <h6>Sitemap</h6>
    <ul class="sitemap"><li>Home</li><li>Apartments</li><li>Location</li><li>Services</li><li>Gallery</li><li>News</li><li>Exclusive Offers &amp; Tours</li><li>For Families</li><li>Contact Us</li></ul>
  </div>
  <div class="col" style="left:344px;width:230px">
    <h6>Contact Us</h6>
    <div class="contact-line"><svg viewBox="0 0 24 24"><path d="M12 2a7 7 0 0 0-7 7c0 5 7 13 7 13s7-8 7-13a7 7 0 0 0-7-7z" fill="#b49b5c"/><circle cx="12" cy="9" r="2.5" fill="#111"/></svg><div><span class="gold">Vltava Suites</span><br>Karlova 48 110 00 Prague<br>CZECH Republic</div></div>
    <div class="contact-line"><svg viewBox="0 0 24 24"><path d="M6 2l4 4-2 3a11 11 0 0 0 7 7l3-2 4 4-3 4C10 22 2 14 2 5z" fill="#b49b5c"/></svg><div>+ 420 600 123 456</div></div>
    <div class="contact-line"><svg viewBox="0 0 24 24"><rect x="2" y="5" width="20" height="14" fill="#b49b5c"/><path d="M2 5l10 8 10-8" stroke="#111" stroke-width="1.5" fill="none"/></svg><div>stay@vltavasuites.example</div></div>
    <div class="socials" aria-label="Social media links"><span></span><span></span><span></span></div>
  </div>
  <div class="col news" style="left:608px">
    <h6>Newsletter</h6>
    <p>Would you like to receive exclusive access to articles &amp; regular monthly newsletter?</p>
    <div class="input">Enter Name *</div>
    <div class="input">Enter Email *</div>
    <div class="subscribe">Subscribe</div>
  </div>
  <div class="col" style="left:876px;top:96px;width:250px">
    <div class="footer-brand">VLTAVA<br>SUITES</div>
    <p>@VLTAVA SUITES - 2017 . All Right Reserved.</p>
  </div>
</footer>

</body>
</html>
```